Website for Apartment Rental in Prague

I would like to create designs of my website focused on luxury apartment rentals in Prague, Czech Republic. I created initial mock-ups, They are all attached. I need to design homepage and subpage. The mock-ups were created by combining elements from different websites that I liked but I need you to create a design that is unique and original. The attached files a only a guidance for the structure of the website but not for the design. Try to be creative.

Apartment

```html
<!DOCTYPE html>
<html lang="en">
<head>
<meta charset="utf-8">
<title>Le Songe – Luxury Apartment Rentals In Prague</title>
<link href="https://fonts.googleapis.com/css2?family=Merriweather:ital,wght@0,300;0,400;0,700;1,300;1,400;1,700&display=swap" rel="stylesheet">
<style>
:root{
  --gold:#c98a34;
  --gold-dark:#b07628;
  --ink:#222222;
  --muted:#9a9a9a;
  --line:#e6e6e6;
  --paper:#ffffff;
  --mist:#f6f6f6;
  --hero-a:#2a2119;
  --hero-b:#4a3a2b;
}
*{margin:0;padding:0;box-sizing:border-box}
html,body{width:1200px;height:3297px;overflow:hidden}
body{font-family:'Merriweather',Georgia,serif;color:var(--ink);background:var(--paper);position:relative}
a{color:inherit;text-decoration:none}

/* header */
.topbar{position:absolute;top:0;left:0;width:1200px;height:40px;font-size:10px;color:#444}
.topbar .contact{position:absolute;left:120px;top:12px;display:flex;gap:32px}
.topbar .contact span{display:flex;align-items:center;gap:6px}
.topbar .lang{position:absolute;right:126px;top:10px;display:flex;align-items:center;gap:10px}
.topbar .lang .select{border:1px solid #bbb;padding:1px 18px 1px 6px;font-size:10px;position:relative}
.topbar .lang .select::after{content:"";position:absolute;right:6px;top:6px;border:3px solid transparent;border-top-color:#666}
.brand{position:absolute;left:520px;top:0;width:160px;height:86px;background:var(--paper);text-align:center;z-index:3;border-radius:0 0 8px 8px}
.brand .name{font-weight:400;font-size:18px;color:var(--ink);margin-top:12px}
.brand .sub{font-size:10px;color:#555;margin-top:4px}
.brand .url{font-size:10px;color:#555;margin-top:2px}
.mainnav{position:absolute;top:40px;left:0;width:1200px;height:44px;border-top:1px solid var(--line);font-size:11px}
.mainnav a{position:absolute;top:15px}

/* hero */
.hero{position:absolute;top:84px;left:0;width:1200px;height:510px}
.hero .photo{position:absolute;inset:0;background:radial-gradient(ellipse at 50% 60%,#5a4634 0%,var(--hero-b) 35%,var(--hero-a) 100%)}
.hero h1{position:absolute;top:172px;width:100%;text-align:center;font-weight:400;font-style:italic;font-size:34px;color:#fff}
.hero h1 em{color:var(--gold);font-style:italic}
.booking .label{position:absolute;top:262px;font-size:11px;color:#eee}
.booking .field{position:absolute;top:284px;height:46px;background:rgba(0,0,0,.35);border:1px solid rgba(255,255,255,.25);color:#eee;font-size:11px;display:flex;align-items:center;padding-left:12px;gap:10px}
.booking .field.sel::after{content:"";position:absolute;right:10px;top:20px;border:4px solid transparent;border-top-color:#ddd}
.booking .go{position:absolute;top:284px;left:892px;width:174px;height:46px;background:var(--gold);color:#fff;font-size:12px;font-weight:700;display:flex;align-items:center;justify-content:center}
.dots{position:absolute;top:463px;left:0;width:100%;display:flex;justify-content:center;gap:10px}
.dots i{width:10px;height:10px;border:1.5px solid #fff;border-radius:50%}
.dots i.on{border-color:var(--gold)}

/* sections */
.section-title{text-align:center;font-weight:700;font-style:italic;font-size:26px}
.section-title::after{content:"";display:block;width:120px;height:1px;background:#ddd;margin:18px auto 0}
.welcome{position:absolute;top:594px;left:0;width:1200px;height:374px;background:var(--mist)}
.welcome .section-title{margin-top:58px}
.welcome p{width:860px;margin:22px auto 0;text-align:center;font-style:italic;font-weight:300;font-size:12px;line-height:19px;color:var(--muted)}
.btn{display:flex;align-items:center;justify-content:center;background:var(--gold);color:#fff;font-size:12px;font-weight:400}
.welcome .btn{width:176px;height:42px;margin:38px auto 0;font-weight:700}

.latest{position:absolute;top:968px;left:0;width:1200px;height:1117px;background:var(--paper)}
.latest .section-title{margin-top:46px}
.featured{position:absolute;top:2085px;left:0;width:1200px;height:675px;background:var(--mist)}
.featured .section-title{margin-top:52px}

.card{position:absolute;width:308px;height:412px;background:var(--paper);border:1px solid #ececec;box-shadow:0 1px 3px rgba(0,0,0,.06);text-align:center}
.card .photo{height:216px;position:relative}
.card .view{position:absolute;left:88px;top:88px;width:132px;height:36px}
.card h3{font-size:12px;font-weight:400;line-height:20px;margin-top:22px;padding:0 30px}
.card .desc{font-size:9px;font-style:italic;font-weight:300;color:#aaa;line-height:14px;margin-top:8px;padding:0 70px}
.card .price{font-size:24px;margin-top:14px}
.card .book{width:126px;height:36px;margin:12px auto 0}
.p1{background:linear-gradient(160deg,#8a7a6a,#c9b59a 50%,#6b5848)}
.p2{background:linear-gradient(160deg,#e6e3de,#c7c1b6 55%,#8f7e6c)}
.p3{background:linear-gradient(160deg,#c8b28c,#a68a63 50%,#5d4a36)}
.p4{background:linear-gradient(160deg,#5a4a3c,#bfb3a3 55%,#6b5a48)}
.p5{background:linear-gradient(160deg,#2e2620,#6b6058 55%,#a49a90)}
.p6{background:linear-gradient(160deg,#d8d0c4,#8c7a66 55%,#4a3c30)}
.p7{background:linear-gradient(160deg,#6a6360,#b9ada0 55%,#e9e4dc)}
.p8{background:linear-gradient(160deg,#c79a62,#8a5a32 55%,#e4d3bb)}
.p9{background:linear-gradient(160deg,#2c3a4e,#6a5a48 55%,#1e1a16)}

/* testimonial */
.testimonial{position:absolute;top:2760px;left:0;width:1200px;height:423px}
.testimonial .bg{position:absolute;inset:0;background:linear-gradient(90deg,#3a2c20,#5c4836 55%,#3e3126)}
.testimonial .accent{position:absolute;left:190px;top:100px;width:286px;height:262px;background:var(--gold)}
.testimonial .frame{position:absolute;left:160px;top:68px;width:282px;height:248px;background:#fff;padding:8px}
.testimonial .frame div{width:100%;height:100%;background:linear-gradient(170deg,#8aa84a,#b9c98a 50%,#d9d4c8)}
.testimonial .who{position:absolute;left:545px;top:92px;width:490px;text-align:center;color:#fff}
.testimonial .who h4{font-size:28px;font-weight:300;font-style:italic}
.testimonial .who .role{font-size:11px;font-style:italic;margin-top:6px}
.testimonial .who p{font-size:11px;font-style:italic;font-weight:300;line-height:19px;margin-top:30px}
.testimonial .arrows{position:absolute;left:756px;top:312px;display:flex;gap:4px}

/* footer */
.footer{position:absolute;top:3183px;left:0;width:1200px;height:114px;background:var(--paper);font-size:10px;font-style:italic}
.footer > *{position:absolute;top:50px}
.footer .social{left:404px;top:44px;display:flex;align-items:center;gap:10px}
.footer .pay{left:644px;top:46px;display:flex;align-items:center;gap:6px}
.footer .pay i{width:36px;height:22px;border:1px solid #ccc;border-radius:2px;background:#eef1f6}
.footer .pay i:first-child{margin-left:24px}
.footer .legal{left:938px;display:flex;gap:10px}
</style>
</head>
<body>

<header>
  <div class="topbar">
    <div class="contact">
      <span><svg width="12" height="9" viewBox="0 0 12 9"><rect x=".5" y=".5" width="11" height="8" fill="none" stroke="#c98a34"/><path d="M.5 .5 6 5l5.5-4.5" fill="none" stroke="#c98a34"/></svg>booking@vltavastays.com</span>
      <span><svg width="10" height="10" viewBox="0 0 10 10"><path d="M2 0 4 2.5 3 4c.8 1.4 1.8 2.4 3 3l1.5-1L10 8 8.5 10C4 9.5.5 6 0 1.5Z" fill="#c98a34"/></svg>+420 700 000 123</span>
    </div>
    <div class="lang">Language <span class="select">En</span></div>
  </div>
  <div class="brand">
    <div class="name">Le Songe</div>
    <div class="sub">Apartments Prague</div>
    <div class="url">vltavastays.com</div>
  </div>
  <nav class="mainnav">
    <a style="left:123px">Apartments</a>
    <a style="left:213px">Location</a>
    <a style="left:286px">Services</a>
    <a style="left:358px">Gallery</a>
    <a style="left:730px">News</a>
    <a style="left:787px">Exclusive Offers&amp; Tours</a>
    <a style="left:936px">For Families</a>
    <a style="left:1029px">Contact Us</a>
  </nav>
</header>

<section class="hero">
  <div class="photo" role="img" aria-label="Photo of a luxurious bedroom with chandelier and upholstered bed"></div>
  <h1><em>Luxury Apartment</em> Rentals In Prague</h1>
  <form class="booking">
    <span class="label" style="left:138px">Check In Date</span>
    <span class="label" style="left:299px">Check Out Date</span>
    <span class="label" style="left:466px">Adults</span>
    <span class="label" style="left:528px">Children</span>
    <span class="label" style="left:591px">Infants</span>
    <span class="label" style="left:653px">Promotional Code</span>
    <div class="field" style="left:136px;width:156px"><svg width="11" height="11" viewBox="0 0 11 11"><rect x=".5" y="1.5" width="10" height="9" fill="none" stroke="#c98a34"/><path d="M.5 4h10" stroke="#c98a34"/></svg>20-11-2017</div>
    <div class="field" style="left:299px;width:156px"><svg width="11" height="11" viewBox="0 0 11 11"><rect x=".5" y="1.5" width="10" height="9" fill="none" stroke="#c98a34"/><path d="M.5 4h10" stroke="#c98a34"/></svg>20-11-2017</div>
    <div class="field sel" style="left:466px;width:55px">2</div>
    <div class="field sel" style="left:528px;width:57px">1</div>
    <div class="field sel" style="left:591px;width:57px">1</div>
    <div class="field" style="left:653px;width:226px">2879006A</div>
    <div class="go">Check Availability</div>
  </form>
  <div class="dots"><i class="on"></i><i></i><i></i><i></i></div>
</section>

<section class="welcome">
  <h2 class="section-title">Welcome to Le Songe</h2>
  <p>At vero eos et accusamus et iusto odio dignissimos ducimus qui blanditiis praesentium voluptatum deleniti atque corrupti quos dolores et quas molestias excepturi sint occaecati cupiditate non provident, similique sunt in culpa qui officia deserunt mollitia animi, id est laborum et dolorum fuga. Et harum quidem rerum facilis est et expedita distinctio. Nam libero tempore, cum soluta nobis est eligendi optio cumque nihil impedit quo minus id quod maxime placeat facere possimus, omnis voluptas assumenda est, omnis dolor repellendus. Temporibus autem quibusdam et aut officiis debitis</p>
  <a class="btn">Learn More</a>
</section>

<section class="latest">
  <h2 class="section-title">Our Latest Apartments</h2>
  <article class="card" style="left:108px;top:162px"><div class="photo p1" role="img" aria-label="Photo of a living room with chandelier"><a class="btn view">View Details</a></div><h3>Brand New Luxury Living Stunning Contemporary Design</h3><p class="desc">At vero eos et accusamus et iusto odio dignissimos ducimus</p><div class="price">$263</div><a class="btn book">Book Now</a></article>
  <article class="card" style="left:442px;top:162px"><div class="photo p2" role="img" aria-label="Photo of a bright white living room"><a class="btn view">View Details</a></div><h3>Brand New Luxury Living Stunning Contemporary Design</h3><p class="desc">At vero eos et accusamus et iusto odio dignissimos ducimus</p><div class="price">$263</div><a class="btn book">Book Now</a></article>
  <article class="card" style="left:774px;top:162px"><div class="photo p3" role="img" aria-label="Photo of a bedroom with city view"><a class="btn view">View Details</a></div><h3>Brand New Luxury Living Stunning Contemporary Design</h3><p class="desc">At vero eos et accusamus et iusto odio dignissimos ducimus</p><div class="price">$263</div><a class="btn book">Book Now</a></article>
  <article class="card" style="left:108px;top:609px"><div class="photo p4" role="img" aria-label="Photo of a classic living room with sofas"><a class="btn view">View Details</a></div><h3>Brand New Luxury Living Stunning Contemporary Design</h3><p class="desc">At vero eos et accusamus et iusto odio dignissimos ducimus</p><div class="price">$263</div><a class="btn book">Book Now</a></article>
  <article class="card" style="left:442px;top:609px"><div class="photo p5" role="img" aria-label="Photo of a dark modern lounge"><a class="btn view">View Details</a></div><h3>Brand New Luxury Living Stunning Contemporary Design</h3><p class="desc">At vero eos et accusamus et iusto odio dignissimos ducimus</p><div class="price">$263</div><a class="btn book">Book Now</a></article>
  <article class="card" style="left:774px;top:609px"><div class="photo p6" role="img" aria-label="Photo of an open kitchen with pendant lights"><a class="btn view">View Details</a></div><h3>Brand New Luxury Living Stunning Contemporary Design</h3><p class="desc">At vero eos et accusamus et iusto odio dignissimos ducimus</p><div class="price">$263</div><a class="btn book">Book Now</a></article>
</section>

<section class="featured">
  <h2 class="section-title">Featured Apartments</h2>
  <article class="card" style="left:108px;top:152px"><div class="photo p7" role="img" aria-label="Photo of a living room with stone wall"><a class="btn view">View Details</a></div><h3>Brand New Luxury Living Stunning Contemporary Design</h3><p class="desc">At vero eos et accusamus et iusto odio dignissimos ducimus</p><div class="price">$263</div><a class="btn book">View Details</a></article>
  <article class="card" style="left:442px;top:152px"><div class="photo p8" role="img" aria-label="Photo of a kitchen with bar stools"><a class="btn view">View Details</a></div><h3>Brand New Luxury Living Stunning Contemporary Design</h3><p class="desc">At vero eos et accusamus et iusto odio dignissimos ducimus</p><div class="price">$263</div><a class="btn book">View Details</a></article>
  <article class="card" style="left:774px;top:152px"><div class="photo p9" role="img" aria-label="Photo of a lounge with large windows at dusk"><a class="btn view">View Details</a></div><h3>Brand New Luxury Living Stunning Contemporary Design</h3><p class="desc">At vero eos et accusamus et iusto odio dignissimos ducimus</p><div class="price">$263</div><a class="btn book">View Details</a></article>
</section>

<section class="testimonial">
  <div class="bg" role="img" aria-label="Photo of a warmly lit apartment lounge"></div>
  <div class="accent"></div>
  <div class="frame"><div role="img" aria-label="Portrait photo of the guest"></div></div>
  <div class="who">
    <h4>Daniel Horak</h4>
    <div class="role">Company Name</div>
    <p>At vero eos et accusamus et iusto odio dignissimos ducimus qui blanditiis praesentium voluptatum deleniti atque corrupti quos dolores et quas molestias excepturi sint occaecati cupiditate non provident, similique sunt in culpa qui officia deserunt mollitia animi, id est laborum et dolorum fuga. Et harum quidem rerum facilis est et expedita distinctio. Nam libero tempore, cum soluta nobis est eligendi</p>
  </div>
  <div class="arrows">
    <svg width="20" height="20" viewBox="0 0 20 20"><circle cx="10" cy="10" r="9" fill="none" stroke="#fff" stroke-width="1.5"/><path d="M11.5 6 7.5 10l4 4" fill="none" stroke="#fff" stroke-width="1.5"/></svg>
    <svg width="20" height="20" viewBox="0 0 20 20"><circle cx="10" cy="10" r="9" fill="none" stroke="#fff" stroke-width="1.5"/><path d="M8.5 6l4 4-4 4" fill="none" stroke="#fff" stroke-width="1.5"/></svg>
  </div>
</section>

<footer class="footer">
  <span style="left:95px">© 2017 Company Name | All Rights Reserved</span>
  <div class="social">Connect With Us
    <svg width="28" height="28" viewBox="0 0 28 28"><circle cx="14" cy="14" r="13" fill="#111"/></svg>
    <svg width="28" height="28" viewBox="0 0 28 28"><circle cx="14" cy="14" r="13" fill="#111"/></svg>
  </div>
  <div class="pay">Payments<i></i><i></i><i></i><i></i></div>
  <div class="legal"><span>Terms Of Use</span><span>|</span><span>Privacy Policy</span></div>
  <svg style="left:1140px;top:48px" width="14" height="10" viewBox="0 0 14 10"><path d="M2 8 7 3l5 5" fill="none" stroke="#333" stroke-width="1.5"/></svg>
</footer>

</body>
</html>
```